Computer consultant business card

Bexil Software is a newly started computer consulting company. It's a small one-man company that provides mostly Vornix applications but also websites in collaboration with designers. I'm running this company on the side of full time university studies.

I want the final design to be clean and memorable. Be creative! :)

Some inspiration:
http://www.pixelmarta.com/design/48317
http://www.pixelmarta.com/design/2739164/business-card-design-by-frostlynk
http://www.pixelmarta.com/design/604281/business-card-design-by-koralind-vestrabanu

See attachment for my company logo.
Updates

I would like to thank everyone for submitting! I'll need a couple of days to review and ultimately select a design.

Target Market(s)

Non-technical entrepreneurs and small companies.

Industry/Entity Type

University

Requirements
Must have
• My company logo.
In any way, both colors from my logo.
First- and last name, e-mail and phone number.
Double-sided design.
Nice to have
• Something creative with the symbol in my logo

```html
<!DOCTYPE html>
<html lang="en">
<head>
<meta charset="utf-8">
<title>Qelvo – Business Card Set</title>
<link rel="stylesheet" href="https://fonts.googleapis.com/css2?family=Jost:wght@400;500;600&display=swap">
<style>
  :root {
    --backdrop: #a98458;
    --ink: #2f2d2e;
    --brand-blue: #4a74bd;
    --paper: #ffffff;
    --muted: #3a3a3a;
    --night: #050505;
    --slate-top: #2b2c31;
    --slate-bottom: #4c5a80;
    --label: #1d1a17;
  }
  * { margin: 0; padding: 0; box-sizing: border-box; }
  html, body { width: 1200px; height: 788px; overflow: hidden; }
  body {
    position: relative;
    background: var(--backdrop);
    font-family: "Jost", "Futura", sans-serif;
  }
  .side-label {
    position: absolute;
    width: 526px;
    text-align: center;
    font-size: 21px;
    color: var(--label);
    font-weight: 400;
  }
  .card {
    position: absolute;
    width: 526px;
    height: 299px;
    border-radius: 20px;
    overflow: hidden;
    box-shadow: 0 4px 10px rgba(0,0,0,0.35);
  }
  .card--front { left: 53px; top: 75px; background: var(--paper); }
  .card--back-light { left: 622px; top: 75px; background: var(--paper); }
  .card--back-night { left: 53px; top: 446px; background: var(--night); }
  .card--back-slate {
    left: 622px; top: 446px;
    background: radial-gradient(ellipse 90% 120% at 75% 100%, var(--slate-bottom) 0%, #3c4357 55%, var(--slate-top) 100%);
  }
  .texture {
    position: absolute;
    inset: 0;
    background:
      radial-gradient(ellipse 45% 45% at 25% 0%, rgba(140,140,140,0.45), transparent 70%),
      radial-gradient(ellipse 40% 45% at 78% 92%, rgba(150,140,140,0.45), transparent 70%);
  }
  .brand {
    position: absolute;
    display: flex;
    align-items: center;
  }
  .brand__dot {
    border-radius: 50%;
    background: var(--brand-blue);
    flex: none;
  }
  .brand__name {
    font-weight: 500;
    color: var(--ink);
    line-height: 1;
    letter-spacing: 0.5px;
  }
  .brand--on-dark .brand__name { color: var(--paper); }

  .card--front .brand { left: 125px; top: 60px; gap: 18px; }
  .card--front .brand__dot { width: 74px; height: 74px; }
  .card--front .brand__name { font-size: 58px; }

  .card--back-light .brand,
  .card--back-night .brand,
  .card--back-slate .brand { left: 103px; top: 92px; gap: 23px; }
  .card--back-light .brand__dot,
  .card--back-night .brand__dot,
  .card--back-slate .brand__dot { width: 106px; height: 106px; }
  .card--back-light .brand__name,
  .card--back-night .brand__name,
  .card--back-slate .brand__name { font-size: 84px; }

  .name-band {
    position: absolute;
    left: 0; top: 182px;
    width: 450px; height: 35px;
    background: var(--ink);
    color: var(--paper);
    display: flex;
    align-items: center;
    padding-left: 74px;
    font-size: 18px;
    font-weight: 600;
    white-space: nowrap;
  }
  .name-band__role { font-size: 13px; font-weight: 400; margin-left: 6px; }
  .accent-block {
    position: absolute;
    left: 458px; top: 182px;
    width: 68px; height: 35px;
    background: var(--brand-blue);
  }
  .contact {
    position: absolute;
    left: 87px; top: 258px;
    display: flex;
    gap: 18px;
    font-size: 15px;
    color: var(--muted);
    white-space: nowrap;
  }
  .contact__item { display: flex; align-items: center; gap: 6px; }
  .contact__item svg { width: 11px; height: 11px; fill: var(--muted); }

  .web-address {
    position: absolute;
    left: 0; right: 0;
    top: 248px;
    text-align: center;
    font-size: 18px;
    letter-spacing: 3px;
    color: var(--muted);
  }
  .card--back-night .web-address,
  .card--back-slate .web-address { top: 252px; color: var(--paper); }
</style>
</head>
<body>
  <div class="side-label" style="left:53px; top:33px;">Front</div>
  <div class="side-label" style="left:622px; top:33px;">Back - 1</div>
  <div class="side-label" style="left:53px; top:404px;">Back - 2</div>
  <div class="side-label" style="left:622px; top:404px;">Back - 3</div>

  <section class="card card--front">
    <div class="brand">
      <span class="brand__dot"></span>
      <span class="brand__name">qelvo</span>
    </div>
    <div class="name-band">First Name + Last Name,<span class="name-band__role">Designation</span></div>
    <div class="accent-block"></div>
    <div class="contact">
      <span class="contact__item">
        <svg viewBox="0 0 24 24"><path d="M6.6 10.8a15 15 0 0 0 6.6 6.6l2.2-2.2c.3-.3.7-.4 1-.2 1.1.4 2.3.6 3.6.6.6 0 1 .4 1 1V20c0 .6-.4 1-1 1A17 17 0 0 1 3 4c0-.6.4-1 1-1h3.5c.6 0 1 .4 1 1 0 1.3.2 2.5.6 3.6.1.3 0 .7-.2 1z"/></svg>
        +12 345 6789
      </span>
      <span class="contact__item">
        <svg viewBox="0 0 24 24"><path d="M2 5h20v14H2z M3 6l9 7 9-7" /></svg>
        info@qelvosoft.com
      </span>
    </div>
  </section>

  <section class="card card--back-light">
    <div class="brand">
      <span class="brand__dot"></span>
      <span class="brand__name">qelvo</span>
    </div>
    <div class="web-address">www.qelvosoft.com</div>
  </section>

  <section class="card card--back-night">
    <div class="texture" role="img" aria-label="Perforated metal dot pattern lit softly at top left and bottom right"></div>
    <div class="brand brand--on-dark">
      <span class="brand__dot"></span>
      <span class="brand__name">qelvo</span>
    </div>
    <div class="web-address">www.qelvosoft.com</div>
  </section>

  <section class="card card--back-slate">
    <div class="brand brand--on-dark">
      <span class="brand__dot"></span>
      <span class="brand__name">qelvo</span>
    </div>
    <div class="web-address">www.qelvosoft.com</div>
  </section>
</body>
</html>
```